Business Cards for new orthopaedic surgery practice

My husband and I are starting our own orthopaedic surgery practice. We are looking for a business card that is uniform, but one will have my name/title and the other will have his. You can just create one design with my name on it for now. But when I choose your design as the winning design I will ask that you add another copy with his name/title.

We are looking for classy, simple, elite all in one. We like dark blues/a little gold/yellow. Something that goes with our logo. We want our logo incorporated. Here is all the info you need:
Business name: RV Bone & Vitality Center
Location: 38517 North Willowmere Ave
Palm Hollow, FL 33482
Phone: 954-218-4063
Fax: 954-582-7341
Email: info@myrvbonecare.example

Names: Lydia Vance, M.D.
Board Certified Hand and Upper Extremity Surgeon

Ebo Dansu, M.D.
Board Certified Hip & Knee Replacement/General Orthopaedic Surgeon

Can decide what you want to put on the back. Maybe a slogan:
Steady in Care. Centered on You

I am just going to upload our logo. The only thing is if we select you as the winning design, the location, and phone numbers may change. We will need your help to update that once fully solidified.

Industry/Entity Type

Medical

Contact Information for Business Card

Colors
0054AA
0677BA
7BADD7
CADEEF
E8F1F8
0094D4
00A9DD
6FCCEA
C7EBF8
E9F6FB

Requirements
Must have
• class, appeal,
Should not have
• We want to air on the side of masculine if we are looking at masculine vs. feminine feel. But we still want it classy, sophisticated, and something we will love

```html
<!DOCTYPE html>
<html lang="en">
<head>
<meta charset="utf-8">
<title>RV Bone &amp; Vitality Center – Business Card</title>
<link rel="stylesheet" href="https://fonts.googleapis.com/css2?family=Montserrat:wght@400;500;600;700&display=swap">
<style>
  :root {
    --navy: #16275a;
    --navy-deep: #0e1b44;
    --gold: #c99a3e;
    --gold-light: #e2bd6b;
    --card-top: #f4f6f9;
    --ink: #1e2a55;
    --on-navy: #e4e7ef;
    --page: #e9eaec;
  }
  * { margin: 0; padding: 0; box-sizing: border-box; }
  html, body {
    width: 1200px; height: 887px; overflow: hidden;
    background: var(--page);
    font-family: "Montserrat", sans-serif;
  }
  .card {
    position: absolute; left: 100px; top: 158px;
    width: 1000px; height: 571px;
    border-radius: 28px; overflow: hidden;
    background: var(--card-top);
    box-shadow: 0 10px 30px rgba(0,0,0,.12);
  }
  .card-bg { position: absolute; inset: 0; width: 100%; height: 100%; }
  .name {
    position: absolute; left: 62px; top: 56px;
    font-weight: 700; font-size: 33px; letter-spacing: 1.5px;
    color: var(--gold); text-transform: uppercase; white-space: nowrap;
  }
  .title {
    position: absolute; left: 62px; top: 100px;
    font-size: 20px; line-height: 27px; color: var(--ink);
  }
  .contact {
    position: absolute; left: 58px; top: 312px;
    list-style: none; color: var(--on-navy);
    font-size: 20px; line-height: 27px;
  }
  .contact li { display: flex; align-items: center; gap: 9px; white-space: nowrap; }
  .contact svg { width: 17px; height: 17px; flex: none; }
  .address {
    position: absolute; left: 58px; top: 442px;
    font-size: 20px; line-height: 28px; color: var(--on-navy); font-style: normal;
  }
  .slogan {
    position: absolute; right: 72px; top: 466px;
    font-size: 20px; font-weight: 500; color: var(--gold-light); white-space: nowrap;
  }
  .brand {
    position: absolute; left: 712px; top: 70px;
    width: 220px; height: 220px; border-radius: 50%;
    border: 3px solid var(--gold);
    display: flex; align-items: center; justify-content: center;
    text-align: center; padding: 24px;
  }
  .brand-name {
    font-weight: 600; font-size: 24px; line-height: 31px; color: var(--navy);
    text-transform: uppercase; letter-spacing: 1px;
  }
</style>
</head>
<body>
<section class="card">
  <svg class="card-bg" viewBox="0 0 1000 571" preserveAspectRatio="none" aria-hidden="true">
    <defs>
      <linearGradient id="navyFill" x1="0" y1="0" x2="1" y2="1">
        <stop offset="0" stop-color="#1d3170"/>
        <stop offset="1" stop-color="#0e1b44"/>
      </linearGradient>
      <linearGradient id="goldFill" x1="0" y1="0" x2="1" y2="0">
        <stop offset="0" stop-color="#c99a3e" stop-opacity="0"/>
        <stop offset=".35" stop-color="#c99a3e"/>
        <stop offset="1" stop-color="#d9ac55"/>
      </linearGradient>
    </defs>
    <path d="M0,168 C220,280 520,345 1000,352 L1000,388 C620,385 300,330 140,250 Z" fill="url(#goldFill)"/>
    <path d="M0,168 C200,270 480,345 1000,372 L1000,382 C520,370 220,300 0,176 Z" fill="#ffffff"/>
    <path d="M0,174 C200,280 480,360 1000,380 L1000,571 L0,571 Z" fill="url(#navyFill)"/>
  </svg>

  <h1 class="name">Lydia Vance, M.D</h1>
  <p class="title">Board Certified Hand and<br>Upper Extremity Surgeon</p>

  <div class="brand">
    <span class="brand-name">RV Bone &amp; Vitality Center</span>
  </div>

  <ul class="contact">
    <li><svg viewBox="0 0 24 24"><path fill="#c99a3e" d="M6.6 10.8a15 15 0 0 0 6.6 6.6l2.2-2.2c.3-.3.7-.4 1-.2 1.1.4 2.3.6 3.6.6.6 0 1 .4 1 1V20c0 .6-.4 1-1 1A17 17 0 0 1 3 4c0-.6.4-1 1-1h3.5c.6 0 1 .4 1 1 0 1.2.2 2.4.6 3.6.1.3 0 .7-.2 1z"/></svg>954-218-4063</li>
    <li><svg viewBox="0 0 24 24"><path fill="none" stroke="#c99a3e" stroke-width="2" d="M7 8V3h10v5M5 8h14a2 2 0 0 1 2 2v6h-4v5H7v-5H3v-6a2 2 0 0 1 2-2zM7 14h10"/></svg>954-582-7341</li>
    <li><svg viewBox="0 0 24 24"><path fill="none" stroke="#c99a3e" stroke-width="2" d="M3 6h18v12H3zM3 6l9 7 9-7"/></svg>info@myrvbonecare.example</li>
    <li><svg viewBox="0 0 24 24"><g fill="none" stroke="#c99a3e" stroke-width="1.8"><circle cx="12" cy="12" r="9"/><path d="M3 12h18M12 3c3 3 3 15 0 18M12 3c-3 3-3 15 0 18"/></g></svg>www.myrvbonecare.example</li>
  </ul>

  <address class="address">38517 North Willowmere Ave<br>Palm Hollow, FL 33482</address>

  <p class="slogan">Steady in Care. Centered on You</p>
</section>
</body>
</html>
```